Brell Stone Company Business Cards

Front and Back Business Card - logo and text setup - cool design. I need workable photoshop or illustrator files so I can setup each employee card with design that is created
Updates

Hi everyone, thank you for the great entries. Please no more white and blue cards - there are so many already - black and silver only now please. thanks!

Target Market(s)

Construction Industry - Facility Managers

Industry/Entity Type

Construction

Contact Information for Business Card

I really like contemporary simplistic looks - clean neat....not opposed to seeing some black backrounds

Requirements
Must have
• Logo/website address with design on front only - www.brellstone-example.com (logo attached)
• Back:
• Name/Title/Company Address/Phone/email address
Nice to have
• Cool design
Should not have
• Nothing gimmicky like Fire or Water - since we are a Fire Protection company - it has all been done

```html
<!DOCTYPE html>
<html lang="en">
<head>
<meta charset="utf-8">
<title>Brell Stone Company Business Cards</title>
<link href="https://fonts.googleapis.com/css2?family=Lato:wght@400;700;900&display=swap" rel="stylesheet">
<style>
  :root {
    --ink: #151517;
    --ink-soft: #232326;
    --silver: #c6c8cc;
    --silver-light: #e4e5e8;
    --silver-mid: #9a9da3;
    --backdrop: #55565a;
  }
  * { box-sizing: border-box; margin: 0; padding: 0; }
  html, body {
    width: 1200px; height: 900px; overflow: hidden;
    background: var(--backdrop);
    font-family: "Lato", sans-serif;
  }
  .canvas {
    position: relative; width: 1200px; height: 900px;
    display: flex; flex-direction: column; align-items: center; justify-content: center; gap: 56px;
  }
  .card {
    position: relative; width: 620px; height: 354px; overflow: hidden;
    box-shadow: 0 10px 28px rgba(0,0,0,0.45);
  }
  .card-front { background: var(--ink); }
  .card-back { background: var(--silver-light); }
  .card-shape { position: absolute; inset: 0; width: 620px; height: 354px; }

  .front-brand {
    position: absolute; left: 0; right: 0; top: 118px; text-align: center;
    color: var(--silver); font-weight: 900; font-size: 64px; letter-spacing: -1px; line-height: 1;
  }
  .front-web {
    position: absolute; left: 0; right: 0; top: 232px; text-align: center;
    color: var(--silver-light); font-size: 17px; letter-spacing: 0.5px;
  }

  .back-brand {
    position: absolute; left: 42px; top: 36px;
    color: var(--ink); font-weight: 900; font-size: 54px; letter-spacing: -1px; line-height: 1;
  }
  .address {
    position: absolute; left: 40px; top: 232px; font-style: normal;
    color: var(--silver-light); font-size: 16px; line-height: 1.45;
  }
  .person {
    position: absolute; right: 40px; top: 208px; text-align: right;
  }
  .person-name { color: var(--silver); font-size: 24px; font-weight: 700; line-height: 1.2; }
  .person-title { color: var(--silver-light); font-size: 17px; line-height: 1.4; }
  .contact-list {
    list-style: none; position: absolute; right: 40px; top: 266px; text-align: right;
    color: var(--silver-light); font-size: 16px; line-height: 24px;
  }
  .contact-list li { display: flex; justify-content: flex-end; align-items: center; gap: 10px; }
  .contact-icon { width: 15px; height: 15px; fill: none; stroke: var(--silver); stroke-width: 2; }
  .contact-icon.solid { fill: var(--silver); stroke: none; }
</style>
</head>
<body>
<main class="canvas">
  <section class="card card-front" aria-label="Card front">
    <div class="front-brand">Brell Stone</div>
    <div class="front-web">www.brellstone-example.com</div>
  </section>

  <section class="card card-back" aria-label="Card back">
    <svg class="card-shape" viewBox="0 0 620 354" aria-hidden="true">
      <path d="M0,130 Q300,260 620,150 L620,354 L0,354 Z" fill="var(--ink)"/>
      <path d="M250,198 Q470,206 620,128 L620,140 Q470,216 250,198 Z" fill="var(--silver-mid)"/>
    </svg>
    <div class="back-brand">Brell Stone</div>
    <address class="address">
      48 Harbor Point Road<br>
      Millbrook, NY 10000
    </address>
    <div class="person">
      <div class="person-name">Dana Marlow Ellis</div>
      <div class="person-title">President</div>
    </div>
    <ul class="contact-list">
      <li>(555) 204-7183
        <svg class="contact-icon solid" viewBox="0 0 24 24" aria-hidden="true"><path d="M6.6 10.8a15.1 15.1 0 0 0 6.6 6.6l2.2-2.2c.3-.3.7-.4 1-.2 1.1.4 2.3.6 3.6.6.6 0 1 .4 1 1V20c0 .6-.4 1-1 1A17 17 0 0 1 3 4c0-.6.4-1 1-1h3.5c.6 0 1 .4 1 1 0 1.3.2 2.5.6 3.6.1.3 0 .7-.2 1z"/></svg>
      </li>
      <li>info@brellstone-example.com
        <svg class="contact-icon solid" viewBox="0 0 24 24" aria-hidden="true"><path d="M2 5h20v14H2z"/><path d="M3 6l9 7 9-7" fill="none" stroke="var(--ink)" stroke-width="1.6"/></svg>
      </li>
      <li>www.brellstone-example.com
        <svg class="contact-icon" viewBox="0 0 24 24" aria-hidden="true"><circle cx="12" cy="12" r="9"/><path d="M3 12h18M12 3c3 3 3 15 0 18M12 3c-3 3-3 15 0 18"/></svg>
      </li>
    </ul>
  </section>
</main>
</body>
</html>
```